Card design for orthopaedic surgeons working as The Brightwater Joint Centre

Business cards, letterhead

Colors

Designer to choose colors to be used in the design.

Requirements
Must have
• Late addition.
• Cards letterhead must have logos of
• Crestmoor Lindell College of Surgeons
• Varenwood Bone Health Association
Nice to have
• Back of card to have space for appointment time to be added by hand and some blank space for writing incidental other notes.

```html
<!DOCTYPE html>
<html lang="en">
<head>
<meta charset="utf-8">
<title>The Brightwater Joint Centre – Business Card</title>
<link href="https://fonts.googleapis.com/css2?family=Poppins:wght@400;500&display=swap" rel="stylesheet">
<style>
  :root {
    --navy: #0c3250;
    --navy-deep: #082438;
    --sky: #3f97d6;
    --ink: #1f2f3d;
    --grey-text: #4a4f55;
    --paper: #ffffff;
    --stage: #e6e8eb;
    --badge: #d3dbe3;
    --line-light: rgba(201, 214, 226, 0.45);
  }
  * { margin: 0; padding: 0; box-sizing: border-box; }
  html, body { width: 1200px; height: 900px; overflow: hidden; }
  body {
    background: var(--stage);
    font-family: 'Poppins', sans-serif;
    display: flex; flex-direction: column; align-items: center; justify-content: center;
    gap: 44px;
  }
  .card {
    width: 620px; height: 354px; border-radius: 18px; position: relative;
    box-shadow: 0 10px 26px rgba(0,0,0,0.18);
  }
  .card-front { background: linear-gradient(135deg, #f1f2f3 0%, var(--paper) 55%, #f4f5f6 100%); }
  .card-back { background: linear-gradient(160deg, var(--navy) 0%, var(--navy-deep) 100%); }

  .brand-name {
    font-weight: 400; font-size: 31px; letter-spacing: -0.5px; white-space: nowrap;
    position: absolute; left: 0; right: 0; text-align: center;
  }
  .card-front .brand-name { color: var(--ink); top: 70px; }
  .card-back .brand-name { color: #c9d6e2; top: 62px; }

  .holder { position: absolute; top: 168px; right: 336px; text-align: right; }
  .holder-name { color: var(--sky); font-weight: 500; font-size: 25px; letter-spacing: 0.5px; line-height: 1.1; }
  .holder-role { color: var(--grey-text); font-size: 16px; margin-bottom: 8px; }
  .holder-address { color: var(--grey-text); font-size: 15px; line-height: 1.45; }

  .divider { position: absolute; left: 305px; top: 178px; width: 2px; height: 122px; background: var(--sky); }

  .contact-list {
    list-style: none; position: absolute; left: 326px; top: 180px;
    color: var(--grey-text); font-size: 15.5px; line-height: 1.72;
  }
  .contact-list li { display: flex; align-items: center; gap: 9px; }
  .contact-list svg { width: 12px; height: 12px; flex: none; }

  .member-badges { position: absolute; left: 40px; bottom: 30px; display: flex; gap: 12px; }
  .member-badge { width: 38px; height: 38px; border-radius: 50%; background: var(--badge); }

  .note-lines { position: absolute; left: 70px; right: 70px; top: 150px; }
  .note-line { height: 1px; background: var(--line-light); margin-bottom: 38px; }
  .note-line.short { width: 55%; }
</style>
</head>
<body>
  <section class="card card-front" aria-label="Business card front">
    <div class="brand-name">The Brightwater Joint Centre</div>

    <div class="holder">
      <div class="holder-name">DANIEL HARROW</div>
      <div class="holder-role">Director</div>
      <div class="holder-address">48 Larkspur Lane<br>Dunmore, TN 37510</div>
    </div>

    <div class="divider"></div>

    <ul class="contact-list">
      <li>
        <svg viewBox="0 0 12 12" aria-hidden="true"><path d="M2.5 1 L4.5 1 L5.2 3.6 L4 4.6 Q5 7 7.4 8 L8.4 6.8 L11 7.5 L11 9.5 Q10.5 11 9 11 Q1 10 1 2.5 Q1 1 2.5 1Z" fill="var(--sky)"/></svg>
        210-555-0147
      </li>
      <li>
        <svg viewBox="0 0 12 12" aria-hidden="true"><rect x="3" y="0.8" width="6" height="10.4" rx="1.2" fill="none" stroke="var(--sky)" stroke-width="1.4"/><circle cx="6" cy="9.2" r="0.7" fill="var(--sky)"/></svg>
        210-555-0199
      </li>
      <li>
        <svg viewBox="0 0 12 12" aria-hidden="true"><rect x="0.8" y="2.5" width="10.4" height="7" rx="1" fill="none" stroke="var(--sky)" stroke-width="1.3"/><path d="M1 3 L6 6.6 L11 3" fill="none" stroke="var(--sky)" stroke-width="1.3"/></svg>
        info@brightwaterjoint.com
      </li>
      <li>
        <svg viewBox="0 0 12 12" aria-hidden="true"><circle cx="6" cy="6" r="5" fill="none" stroke="var(--sky)" stroke-width="1.2"/><ellipse cx="6" cy="6" rx="2.2" ry="5" fill="none" stroke="var(--sky)" stroke-width="1"/><path d="M1 6 H11" stroke="var(--sky)" stroke-width="1"/></svg>
        www.brightwaterjoint.com
      </li>
    </ul>

    <div class="member-badges">
      <div class="member-badge" role="img" aria-label="Crestmoor Lindell College of Surgeons membership badge"></div>
      <div class="member-badge" role="img" aria-label="Varenwood Bone Health Association membership badge"></div>
    </div>
  </section>

  <section class="card card-back" aria-label="Business card back">
    <div class="brand-name">The Brightwater Joint Centre</div>
    <div class="note-lines" aria-label="Space for appointment time and notes">
      <div class="note-line"></div>
      <div class="note-line"></div>
      <div class="note-line"></div>
      <div class="note-line short"></div>
    </div>
  </section>
</body>
</html>
```